Need a new Website Design

We are changing the project requirements because we did not get desired design. Here are the new requirements.

We sell machinery used to compact recyclable materials into neat and tidy bales. We also sell accessories and consumables related this equipment.

Our existing website is:
http://www.kelvopress.com

Our company name is 'NIngbo Kelvopress Machinery co. LTD' and we only need 1 page designed creatively. The homepage should introduce our company and what we do, as well as direct them to search or browse our balers and baler related products. It should also exude a sense of credibility, confidence and success.

Important Notes:
Links to the logo files:
- Adobe Illustrator format: http://www.kelvopress.com/assets/Kelvopress.ai
- Corel Draw format: http://www.kelvopress.com/assets/Kelvopress.cdr

Links to the Kelvopress proprietary font:
- Adobe Illustrator format: http://www.kelvopress.com/assets/Kelvopress-font.ai
- Corel Draw format: http://www.kelvopress.com/assets/Kelvopress-font.cdr

Our marketing photos can be downloaded here: http://qlnk.example/TRbwM7
You can see an example of the homepage on http://www.kelvopress.com/home-test/
Proprietary images are available here: http://www.pictovault.example/photos/31847720@N09/

It is important that the user should be able to access his needed baler either by type (vertical/horizontal baler) or applications straight from the homepage.

Important:
one general comment which I should have brought up from the beginning is that google analytics shows that most clients go about doing their business on our site by clicking on baler types, vertical balers, horizontal balers, and waste applications. They either want to see the whole product range first, or they already set on a manual or vertical baler, or they have no idea and thus prefer to browse the waste applications to pin down the type of waste they have have that needs to be baled. It would be good to have all of our balers and applications listed in the home page. This is one way to do it but by no means is it the right way:

http://www.kelvopress.com/home-test/

Target Market(s)

Industrial

Industry/Entity Type

Marketing

Requirements
Must have
• The logo and machine colors should be used for the color scheme. It must appeal to an international and eclectic market of recyclers, traders and small businesses. Other than that it should look and feel authentic.
Nice to have
• N/A
Should not have
• N/A

```html
<!DOCTYPE html>
<html lang="en">
<head>
<meta charset="utf-8">
<title>Kelvopress – Baling Machinery</title>
<link href="https://fonts.googleapis.com/css2?family=Open+Sans:wght@400;600;700&family=Roboto+Condensed:wght@400;700&display=swap" rel="stylesheet">
<style>
:root{
  --navy:#1b2a38;
  --navy-deep:#0f1c28;
  --blue:#1e73b8;
  --blue-light:#3a9ad8;
  --orange:#f0771e;
  --green:#1a8a3c;
  --lime:#a8c72a;
  --lime-dark:#8db01e;
  --text:#333;
  --muted:#555;
  --page:#ececec;
  --line:#d5d5d5;
}
*{margin:0;padding:0;box-sizing:border-box}
html,body{width:811px;height:1200px;overflow:hidden}
body{font-family:"Open Sans",Arial,sans-serif;color:var(--text);background:var(--page)}
.page{position:relative;width:811px;height:1200px;overflow:hidden;background:var(--page)}
.hero-bg{position:absolute;left:0;top:0;width:811px;height:345px;background:linear-gradient(180deg,#0d1a26 0%,#16344f 55%,#1f5e8e 100%)}
.hero-band{position:absolute;left:0;top:302px;width:811px;height:43px;background:var(--blue)}
.hero-band::before{content:"";position:absolute;left:0;top:-4px;width:811px;height:4px;background:#fff}
.hero-line{position:absolute;left:0;top:342px;width:811px;height:5px;background:var(--lime)}
.a{position:absolute}
.header{left:87px;top:0;width:637px;height:64px;background:var(--navy);border-radius:0 0 3px 3px}
.brand{left:12px;top:18px;font:700 20px "Roboto Condensed",sans-serif;color:#fff;letter-spacing:1px;display:flex;align-items:center;gap:6px}
.brand i{display:block;width:9px;height:9px;border-radius:50%;background:var(--lime)}
.util{right:14px;top:9px;font:400 7.5px "Open Sans",sans-serif;color:#cfd6dc;display:flex;gap:7px;align-items:center}
.util span.s{display:inline-block;width:10px;height:10px;border-radius:50%;background:var(--lime)}
.import{right:14px;top:38px;font:600 8.5px "Open Sans",sans-serif;color:#fff;display:flex;align-items:center;gap:6px}
.import b{display:block;width:20px;height:20px;border-radius:50%;background:radial-gradient(circle at 40% 35%,#ff6a5a,#c8140c)}
.nav{left:87px;top:74px;width:637px;height:30px;background:linear-gradient(#c4de3e,var(--lime-dark));border-radius:3px;display:flex;align-items:center}
.nav a{font:400 10px "Open Sans",sans-serif;color:#1c2a10;text-decoration:none;padding:0 8px;border-right:1px solid rgba(0,0,0,.15)}
.nav a.home{background:var(--navy);color:#fff;height:30px;line-height:30px;padding:0 10px;margin-left:2px;border:none}
.nav a:nth-last-child(3){border:none}
.search{margin-left:8px;width:104px;height:15px;background:#fff;border:1px solid #9b9b9b;font:400 6.5px "Open Sans";color:#999;padding:2px 5px}
.go{margin-left:3px;width:21px;height:15px;background:var(--blue);color:#fff;font:700 7px "Open Sans";text-align:center;line-height:15px;border-radius:2px}
.hero{left:87px;top:112px;width:637px;height:210px;background:linear-gradient(120deg,#0f4a34 0%,#1f8c4e 45%,#2da25a 70%,#5fb66e 100%);border-radius:3px;overflow:hidden}
.hero-card{left:348px;top:41px;width:289px;height:90px;background:rgba(255,255,255,.88)}
.hero-card p{position:absolute;left:15px;top:23px;font:700 13px "Roboto Condensed",sans-serif;color:#111}
.hero-card p em{font-style:normal;color:var(--blue);font-size:21px}
.hero-card h1{position:absolute;left:15px;top:45px;font:700 27px "Roboto Condensed",sans-serif;color:#111;letter-spacing:.2px}
.col-h{font:700 17px "Roboto Condensed",sans-serif;top:364px;border-bottom:1px solid var(--line);padding-bottom:4px;width:186px}
.photo{top:392px;width:186px;height:165px;background:#fff;border:4px solid #e0e0e0;padding:3px}
.photo div{width:100%;height:100%}
.series{font:700 10.5px "Roboto Condensed",sans-serif;color:#222;top:565px}
ul.list{list-style:none;font:400 7.4px "Open Sans",sans-serif;color:#444}
ul.list li{border-bottom:1px solid #dcdcdc;height:15.3px;line-height:15px;padding-left:8px;position:relative}
ul.list li::before{content:"";position:absolute;left:1px;top:5px;border-left:3px solid var(--blue);border-top:2.5px solid transparent;border-bottom:2.5px solid transparent}
ul.apps li{height:15.8px;line-height:15.5px}
.view{font:400 6.5px "Open Sans";color:var(--blue);top:648px}
.what-h{left:87px;top:680px;font:700 22px "Roboto Condensed",sans-serif;color:var(--blue);border-bottom:1px solid var(--line);width:416px;padding-bottom:2px}
.what-p{left:87px;width:416px;font:400 7.3px/10.2px "Open Sans",sans-serif;color:#444}
.contact{left:87px;top:816px;font:600 10px "Open Sans";color:#333}
.contact b{color:var(--green);font-weight:600}
.btn{width:173px;height:36px;border-radius:3px;border:2px solid #fff;box-shadow:0 1px 3px rgba(0,0,0,.3);font:700 10.5px/11px "Roboto Condensed",sans-serif;color:#fff;text-transform:uppercase;display:flex;align-items:center;padding-left:48px}
.btn.g{background:linear-gradient(#8cc63a,#4f9a1c)}
.btn.b{background:linear-gradient(#5fb4e8,#2582c6)}
.btn.o{background:linear-gradient(#ffb640,#f08a10)}
.ico{position:absolute;left:8px;top:-6px;width:34px;height:38px;border-radius:4px}
.ten{position:absolute;left:6px;top:-4px;font:700 34px "Roboto Condensed";color:#1a1a1a}
.divider{left:524px;top:690px;width:1px;height:310px;background:var(--line)}
.seal{left:548px;top:688px;width:50px;height:50px;border-radius:50%;background:#d8232a}
.warranty{left:614px;top:706px;font:700 18px "Roboto Condensed";color:#1a1a1a}
.test-h{left:545px;top:766px;font:700 17px "Roboto Condensed";color:var(--blue)}
.quote{left:546px;top:797px;width:162px;height:141px;background:var(--navy);color:#fff;padding:12px 11px}
.quote h3{font:600 15px "Open Sans";margin-bottom:6px}
.quote p{font:400 7px/9.8px "Open Sans"}
.quote::after{content:"";position:absolute;left:22px;bottom:-20px;border-top:20px solid var(--navy);border-right:18px solid transparent}
.person-pic{left:548px;top:966px;width:40px;height:34px;background:linear-gradient(#4b6f8f,#a8b9c6);border:2px solid #fff}
.person{left:595px;top:964px;font:700 12px "Roboto Condensed";color:#222;line-height:13px}
.person small{display:block;font:600 7px/9px "Open Sans";color:#555}
.part-h{left:88px;top:1026px;font:700 15.5px "Roboto Condensed";color:#222;border-bottom:1px solid var(--line);width:636px;padding-bottom:4px}
.partners{left:87px;top:1058px;width:637px;height:78px;background:linear-gradient(#fbfbfb,#d6d6d6);border:1px solid #cfcfcf;border-radius:3px;display:flex;justify-content:space-around;align-items:center}
.partners span{display:block;width:56px;height:44px;background:#c4c4c4;border-radius:6px}
.footer{left:87px;top:1145px;width:637px;height:55px;background:linear-gradient(#1e5c8a,#123f63);padding:15px 14px}
.footer nav{font:600 7px "Open Sans";color:#fff;display:flex;gap:5px}
.footer nav i{font-style:normal;color:#7fa7c6}
.footer p{font:400 7px "Open Sans";color:#dde7ef;margin-top:6px}
.footer .mark{position:absolute;right:28px;top:15px;font:700 18px "Roboto Condensed";color:rgba(255,255,255,.35);letter-spacing:1px}
</style>
</head>
<body>
<div class="page">
  <div class="hero-bg"></div>
  <div class="hero-band"></div>
  <div class="hero-line"></div>

  <header class="a header">
    <div class="a brand"><i></i>KELVOPRESS</div>
    <div class="a util">TRACK YOUR ORDER | TECHNICAL SUPPORT | CONTACT US <span class="s"></span><span class="s"></span><span class="s"></span></div>
    <div class="a import"><b></b>IMPORTING FROM CHINA AS EASY AS 123</div>
  </header>

  <nav class="a nav">
    <a class="home">Home</a><a>About us</a><a>Baler Types</a><a>Applications</a><a>Baler Accessories</a><a>Testimonials</a><a>Inquire Now!</a>
    <div class="search">Search...</div><div class="go">GO!</div>
  </nav>

  <section class="a hero" role="img" aria-label="Photo of a large green baling machine line installed in a recycling facility">
    <div class="a hero-card">
      <p>WE OFFER A <em>COMPLETE RANGE</em></p>
      <h1>BAILING MACHINERY</h1>
    </div>
  </section>

  <h2 class="a col-h" style="left:87px;color:var(--blue)">HORIZONTAL BALERS</h2>
  <h2 class="a col-h" style="left:310px;color:var(--orange)">VERTICAL BALERS</h2>
  <h2 class="a col-h" style="left:531px;color:var(--green);width:185px">APPLICATIONS</h2>

  <div class="a photo" style="left:87px"><div role="img" aria-label="Blue fully automatic horizontal baler with a compressed bale" style="background:radial-gradient(circle at 55% 55%,#3f7fc6,#cfe0f2 60%,#fff)"></div></div>
  <div class="a photo" style="left:310px"><div role="img" aria-label="Blue and yellow vertical baler" style="background:radial-gradient(ellipse at 50% 55%,#2a6cc4 0,#f0c83a 20%,#dce8f5 45%,#fff 70%)"></div></div>

  <h3 class="a series" style="left:88px">HORIZONTAL BALER SERIES</h3>
  <ul class="a list" style="left:88px;top:580px;width:182px">
    <li>Fully Automatic Horizontal Baler</li><li>Manual Tie Horizontal Baler</li><li>Top Force Auto-Tie Automatic Baler</li><li>Heavy Duty Horizontal Bagging Baler</li>
  </ul>
  <h3 class="a series" style="left:311px">VERTICAL BALER SERIES</h3>
  <ul class="a list" style="left:311px;top:580px;width:182px">
    <li>Standard Mill Size Baler</li><li>Lifting Chamber Baler</li><li>Long Stroke Baler</li><li>Swivel Twin Baler</li>
  </ul>
  <ul class="a list apps" style="left:531px;top:390px;width:185px">
    <li>Aluminum Alloy Frame/Sheet</li><li>Aluminum Can Baling</li><li>Cardboard Baler (e.g. OCC, Carton)</li><li>Chopped Straw/Hay</li><li>Cotton Seed</li><li>Disposable Tableware</li><li>Drum/Barrel (e.g. Paint Drum, Oil Barrel)</li><li>Foam (Sponge)</li><li>Hollow Plastic (e.g. PET Bottle, PP Container, PVC )</li><li>Leaves</li><li>Mineral Cotton Fiber (Asbestus)</li><li>Natural Fiber (e.g. Coconut Fiber, Palm Fiber )</li><li>Paper (e.g. OMG, ONP, Book, Craft, Paper Trim)</li><li>Peanut Shell</li><li>Plastic Shell (e.g. Computer Shell, Bumper, TV Shell)</li><li>Rice Husk</li>
  </ul>
  <span class="a view" style="left:239px">View All...</span>
  <span class="a view" style="left:461px">View All...</span>
  <span class="a view" style="left:682px">View All...</span>

  <h2 class="a what-h">WHAT WE DO!</h2>
  <p class="a what-p" style="top:718px">Kelvopress, a pioneer baler manufacturer, supplies industry-leading and cost-effective baling solutions for all types of waste material. From small standalone vertical presses to fully automated horizontal lines, we offer a complete range of baling machinery. Our smartly designed machines are CE certified, with top brand hydraulics and electric components. Durability and affordable prices make our machinery stands out among similar baling presses. As a pioneer in the waste recycling market, we help you turn your waste into a new source of profit.</p>
  <p class="a what-p" style="top:773px">Be ready to witness large savings on recycling and waste removal costs. Kelvopress waste specialists work around the hour and across the globe to bring you considerate after-sales service, strict quality standards and long term value for your most challenging waste handling projects.</p>
  <p class="a contact"><b>Contact Us</b> now and our engineers will help tailor a solution, best fit to your needs.</p>

  <div class="a btn g" style="left:110px;top:864px"><span class="ico" role="img" aria-label="Illustration of a support agent" style="background:#e86aa8;border-radius:50%;width:30px;height:34px"></span>How can we<br>help you?</div>
  <div class="a btn g" style="left:310px;top:864px"><span class="ico" role="img" aria-label="Film clapper icon" style="background:#2a2a2a"></span>Videos Library</div>
  <div class="a btn b" style="left:110px;top:912px"><span class="ico" role="img" aria-label="Product catalogue cover" style="background:#8a6a4a"></span>Product<br>Catalogue</div>
  <div class="a btn b" style="left:310px;top:912px"><span class="ico" style="background:#e9e9e9;border-radius:50%;width:34px;height:34px"></span>On VideoHub</div>
  <div class="a btn o" style="left:110px;top:960px;padding-left:50px"><span class="ten">10</span>Reasons for<br>choosing Kelvopress</div>
  <div class="a btn o" style="left:310px;top:960px"><span class="ico" role="img" aria-label="Photo gallery icon" style="background:#f2f2f2"></span>Product Gallery</div>

  <div class="a divider"></div>
  <div class="a seal"></div>
  <div class="a warranty">WARRANTY</div>
  <h2 class="a test-h">TESTIMONIALS</h2>
  <blockquote class="a quote">
    <h3>Hello</h3>
    <p>We'd be happy to send our company informations to your customers so they can ask us about the press-machine.<br>We are very happy with the pressing machine and did not meet any difficulties using it.<br><br>Please let us know if your future clients need reference, we'd be happy to help!</p>
  </blockquote>
  <div class="a person-pic" role="img" aria-label="Photo of the customer's installed baler"></div>
  <div class="a person">Mr.Tarrow<small>Vornel Textilhandel<br>Germany</small></div>

  <h2 class="a part-h">OUR PARTNERS</h2>
  <div class="a partners"><span></span><span></span><span></span><span></span><span></span></div>

  <footer class="a footer">
    <nav>Home <i>|</i> About us <i>|</i> Baler Types <i>|</i> Applications <i>|</i> Baler Accessories <i>|</i> Terms &amp; Conditions</nav>
    <p>© 2013 Kelvopress Machinery Company Limited. All Rights Reserved.</p>
    <div class="mark">KELVOPRESS</div>
  </footer>
</div>
</body>
</html>
```